Varnik Holdings — Business Card Design Brief
Overview
Design a double-sided business card for Varnik Holdings that highlights our two service arms: Varnik Communications (telecommunications) and Varnik Energy (business energy solutions). The card should feel smart and stand out when handed to clients.

Objectives
Showcase our areas of specialty clearly.
Reflect the overall Varnik / Varnik Holdings brand while acknowledging both arms.
Explore using both logos (Communications + Energy) or one unified logo, depending on the design.

Deliverables
One double-sided business card design (front + back).

Content & Copy
Front (preferred): Logo: Varnik / Varnik Holdings
Descriptor: Business Communications | Business Energy
Back:My contact details and company details
Core products: Business Mobile • Telephony • Internet • Business Energy Solutions

Brand & Visual Direction
We have a group logo currently tailored more toward telecoms, plus a separate Varnik Energy logo.
Please explore layouts that use both logos or just one, whichever works best.
Color: I wouldn't mind seeing an option using our the Blue/Purple gradient from our website (varnik-example.co.uk), but also open to non-gradient approaches and other colours..

Overall look: Smart, modern, and distinctive.
Format & Print Specs
Double-sided business card format. (Use a standard size

Must-Haves
Front: Varnik wording or Varnik Holdings wording with atleast 1 logo also on front “Business Communications | Business Energy.”

Back: Contact + company details and core products.
A design that stands out while remaining professional.

Nice-to-Have Options
A gradient version using our site’s Blue/Purple gradient.
A non-gradient version.
A dual-logo treatment versus a single-logo treatment.

Thanks
Owen

```html
<!DOCTYPE html>
<html lang="en">
<head>
<meta charset="utf-8">
<title>Varnik Holdings — Business Card</title>
<link href="https://fonts.googleapis.com/css2?family=Montserrat:wght@800&family=Arimo:wght@400;700&display=swap" rel="stylesheet">
<style>
  :root {
    --navy: #1b1566;
    --green: #3aa935;
    --lime: #b9cc1e;
    --blue: #1565d8;
    --sky: #0cb3e3;
    --deep: #0a58cf;
    --ink: #3d3d44;
    --rule: #c9c9cc;
    --paper: #ffffff;
    --backdrop: #e6e6e6;
  }
  * { box-sizing: border-box; margin: 0; padding: 0; }
  html, body {
    width: 1200px; height: 1200px; overflow: hidden;
    background: var(--backdrop);
    font-family: "Arimo", Arial, sans-serif;
  }
  .canvas { position: relative; width: 1200px; height: 1200px; }

  .card {
    position: absolute; left: 255px; width: 690px; height: 394px;
    overflow: hidden;
  }
  .card--front { top: 158px; background: var(--paper); }
  .card--back {
    top: 652px;
    background: linear-gradient(180deg, var(--sky) 0%, #0d8ede 45%, var(--deep) 100%);
  }

  /* front */
  .wordmark {
    position: absolute; left: 48px; top: 56px;
    font-family: "Montserrat", Arial, sans-serif; font-weight: 800;
    font-size: 58px; letter-spacing: 1px; color: var(--navy); line-height: 1;
  }
  .brand-arm {
    position: absolute; right: 48px; display: flex; align-items: center; gap: 12px;
    width: 200px;
  }
  .brand-arm--energy { top: 52px; }
  .brand-arm--comms { top: 190px; }
  .brand-arm__dot {
    flex: none; width: 64px; height: 64px; border-radius: 50%;
    border: 7px solid currentColor;
  }
  .brand-arm__name { font-family: "Arimo", Arial, sans-serif; font-weight: 700; font-size: 18px; line-height: 1.2; }
  .brand-arm--energy { color: var(--green); }
  .brand-arm--comms { color: var(--blue); }

  .holder { position: absolute; left: 48px; top: 230px; }
  .holder__name {
    font-family: "Montserrat", Arial, sans-serif; font-weight: 800;
    font-size: 25px; color: var(--navy); letter-spacing: 0.5px; line-height: 1.1;
  }
  .holder__role { font-size: 15px; color: var(--green); margin-top: 3px; }

  .divider-rule {
    position: absolute; left: 48px; right: 48px; top: 289px;
    height: 1px; background: var(--rule);
  }
  .contact { position: absolute; top: 301px; font-size: 16px; color: var(--ink); }
  .contact--phones { left: 48px; }
  .contact--web { left: 225px; }
  .contact--address { left: 454px; top: 303px; line-height: 21px; }
  .contact__row { display: flex; align-items: center; gap: 8px; height: 20px; }
  .contact__icon { width: 14px; height: 14px; flex: none; fill: var(--navy); }

  .products-band {
    position: absolute; left: 0; right: 0; bottom: 0; height: 31px;
    background: var(--navy); color: #fff; font-size: 17.5px;
    display: flex; align-items: center; justify-content: center; gap: 8px;
  }

  /* back */
  .service-split {
    position: absolute; inset: 0; display: flex; align-items: center; justify-content: center;
  }
  .service {
    width: 300px; display: flex; flex-direction: column; align-items: center; gap: 26px;
    color: #fff;
  }
  .service__mark { display: flex; align-items: center; gap: 14px; height: 118px; }
  .service__dot {
    width: 110px; height: 110px; border-radius: 50%; border: 10px solid #fff; flex: none;
  }
  .service__name { font-weight: 700; font-size: 20px; line-height: 1.2; }
  .service__label { font-size: 16.5px; letter-spacing: 0.2px; }
  .service-split__line { width: 1px; height: 168px; background: rgba(255,255,255,0.75); }
</style>
</head>
<body>
<main class="canvas">

  <section class="card card--front" aria-label="Card front">
    <div class="wordmark">VARNIK</div>

    <div class="brand-arm brand-arm--energy">
      <span class="brand-arm__dot"></span>
      <span class="brand-arm__name">Varnik<br>Energy</span>
    </div>
    <div class="brand-arm brand-arm--comms">
      <span class="brand-arm__dot"></span>
      <span class="brand-arm__name">Varnik<br>Communications</span>
    </div>

    <div class="holder">
      <div class="holder__name">DANIEL REEVE</div>
      <div class="holder__role">President</div>
    </div>

    <div class="divider-rule"></div>

    <div class="contact contact--phones">
      <div class="contact__row">
        <svg class="contact__icon" viewBox="0 0 24 24"><path d="M6.6 10.8a15.1 15.1 0 0 0 6.6 6.6l2.2-2.2a1 1 0 0 1 1-.25 11.4 11.4 0 0 0 3.6.57 1 1 0 0 1 1 1V20a1 1 0 0 1-1 1A17 17 0 0 1 3 4a1 1 0 0 1 1-1h3.5a1 1 0 0 1 1 1c0 1.25.2 2.45.57 3.6a1 1 0 0 1-.25 1z"/></svg>
        <span>555-210-4831</span>
      </div>
      <div class="contact__row">
        <svg class="contact__icon" viewBox="0 0 24 24"><path d="M7 1h10a2 2 0 0 1 2 2v18a2 2 0 0 1-2 2H7a2 2 0 0 1-2-2V3a2 2 0 0 1 2-2zm0 3v15h10V4zm5 16.2a1 1 0 1 0 0 2 1 1 0 0 0 0-2z"/></svg>
        <span>555-302-7719</span>
      </div>
    </div>

    <div class="contact contact--web">
      <div class="contact__row">
        <svg class="contact__icon" viewBox="0 0 24 24"><path d="M2 5h20v14H2zm2 2v.4l8 5.3 8-5.3V7zm0 2.8V17h16V9.8l-8 5.3z"/></svg>
        <span>info@varnik-example.com</span>
      </div>
      <div class="contact__row">
        <svg class="contact__icon" viewBox="0 0 24 24"><path d="M12 2a10 10 0 1 0 0 20 10 10 0 0 0 0-20zm-1 17.9A8 8 0 0 1 4.2 10L9 14.8v1a2 2 0 0 0 2 2zm6.9-2.5A2 2 0 0 0 16 16h-1v-3a1 1 0 0 0-1-1H8v-2h2a1 1 0 0 0 1-1V7h2a2 2 0 0 0 2-2v-.4a8 8 0 0 1 2.9 12.8z"/></svg>
        <span>www.varnik-example.com</span>
      </div>
    </div>

    <address class="contact contact--address" style="font-style:normal">
      412 Alder Crescent<br>Halden, Canada 218
    </address>

    <div class="products-band">
      <span>Business Mobile</span><span>•</span><span>Telephony</span><span>•</span><span>Internet</span><span>•</span><span>Business Energy Solutions</span>
    </div>
  </section>

  <section class="card card--back" aria-label="Card back">
    <div class="service-split">
      <div class="service">
        <div class="service__mark">
          <span class="service__dot"></span>
          <span class="service__name">Varnik<br>Communications</span>
        </div>
        <div class="service__label">BUSINESS COMMUNICATIONS</div>
      </div>
      <div class="service-split__line"></div>
      <div class="service">
        <div class="service__mark">
          <span class="service__dot"></span>
          <span class="service__name">Varnik<br>Energy</span>
        </div>
        <div class="service__label">BUSINESS ENERGY</div>
      </div>
    </div>
  </section>

</main>
</body>
</html>
```